Business card design for holistic health care clinic

We need a double-sided business card design for our holistic health care clinic that integrates our logo design and also its color scheme. My business is called Valmira. It is an integrative medicine clinic. You have already done the logo for me. Please ensure an elegant and upscale design that is not cluttered, but still has all the necessary information (please see below for details).

Target Market(s)

Wellness, fitness, rehabilitation for educated, well-traveled open-minded clients who are focused on natural, organic, balanced and preventive healthcare and lifestyle.

Industry/Entity Type

Medical

Contact Information for Business Card

Modern, clean.

Number of Pages Required

1 page

Font styles to use
Serif
Sans Serif

Colors

Designer to choose colors to be used in the design.

Requirements
Must have
• Logo on one side, all other information on the other side.
• Other information should include:
• Tobias Wrenfeld - DOE, CPT, LMT
• 4100 East Marrow Drive
• Austin, TX 78119
• 512 555 0148
• 818 555 0192
• info@ValmiraHealth.example
• t.wrenfeld@ValmiraHealth.example
Nice to have
• Darker background on front - but not totally black - shaded/dark gray.

```html
<!DOCTYPE html>
<html lang="en">
<head>
<meta charset="utf-8">
<title>Valmira – Business Card</title>
<link rel="stylesheet" href="https://fonts.googleapis.com/css2?family=Nunito:wght@700&family=Source+Sans+3:wght@400;600&display=swap">
<style>
  :root {
    --page-bg: #e6e4e1;
    --card-dark: #17191d;
    --card-mid: #24272d;
    --blue: #1f7bc4;
    --blue-deep: #0c4f8e;
    --blue-bright: #3a9be0;
    --line-dark: #0b1a2c;
    --text-light: #d3d7dd;
    --text-soft: #aab3bf;
  }
  html, body {
    margin: 0;
    width: 1200px;
    height: 969px;
    overflow: hidden;
    background: var(--page-bg);
  }
  .card {
    position: absolute;
    left: 100px;
    top: 199px;
    width: 1000px;
    height: 571px;
    overflow: hidden;
    background: linear-gradient(160deg, var(--card-mid) 0%, var(--card-dark) 60%);
    box-shadow: 0 14px 40px rgba(0,0,0,0.25);
    font-family: "Source Sans 3", "Helvetica Neue", Arial, sans-serif;
    color: var(--text-light);
  }
  .card__swoosh { position: absolute; inset: 0; }
  .brand {
    position: absolute;
    left: 78px;
    top: 128px;
    color: var(--blue);
  }
  .brand__name {
    font-family: "Nunito", "Helvetica Neue", Arial, sans-serif;
    font-weight: 700;
    font-size: 92px;
    line-height: 1;
    letter-spacing: 2px;
    text-transform: uppercase;
    margin: 0;
  }
  .brand__tagline {
    font-family: "Nunito", "Helvetica Neue", Arial, sans-serif;
    font-weight: 700;
    font-size: 28px;
    margin: 8px 0 0 4px;
    letter-spacing: 0.5px;
  }
  .person {
    position: absolute;
    right: 56px;
    top: 336px;
    text-align: right;
  }
  .person__name {
    font-size: 27px;
    font-weight: 600;
    text-transform: uppercase;
    margin: 0;
    line-height: 1.1;
    letter-spacing: 0.5px;
  }
  .person__creds {
    font-size: 17px;
    color: var(--text-soft);
    margin: 3px 0 0;
  }
  .address {
    position: absolute;
    right: 430px;
    top: 484px;
    text-align: right;
    font-style: normal;
    font-size: 21px;
    line-height: 33px;
    color: var(--text-soft);
  }
  .divider {
    position: absolute;
    left: 586px;
    top: 486px;
    width: 1px;
    height: 60px;
    background: var(--text-soft);
    opacity: 0.6;
  }
  .contacts {
    position: absolute;
    right: 56px;
    top: 418px;
    margin: 0;
    padding: 0;
    list-style: none;
  }
  .contacts__item {
    display: flex;
    justify-content: flex-end;
    align-items: center;
    gap: 12px;
    height: 33px;
    font-size: 21px;
    color: var(--text-soft);
  }
  .contacts__item svg { width: 20px; height: 20px; fill: var(--text-soft); }
  .contacts__item .icon-cut { fill: none; stroke: var(--blue-deep); }
</style>
</head>
<body>
  <section class="card" aria-label="Valmira business card">
    <svg class="card__swoosh" viewBox="0 0 1000 571" preserveAspectRatio="none" aria-hidden="true">
      <defs>
        <linearGradient id="swooshFill" x1="0" y1="1" x2="1" y2="0">
          <stop offset="0" stop-color="#0c4f8e"/>
          <stop offset="0.5" stop-color="#1f7bc4"/>
          <stop offset="1" stop-color="#3a9be0"/>
        </linearGradient>
      </defs>
      <path d="M0,545 C180,420 470,400 680,340 C850,290 960,210 1000,100 L1000,571 L0,571 Z" fill="url(#swooshFill)" opacity="0.85"/>
      <path d="M0,565 C190,440 480,418 690,358 C858,308 966,228 1000,135" fill="none" stroke="#0b1a2c" stroke-width="4"/>
    </svg>

    <div class="brand">
      <h1 class="brand__name">Valmira</h1>
      <p class="brand__tagline">Integrative Holistic Medicine</p>
    </div>

    <div class="person">
      <h2 class="person__name">Tobias Wrenfeld</h2>
      <p class="person__creds">DOE, CPT, LMT</p>
    </div>

    <address class="address">
      4100 East Marrow Drive<br>Austin, TX 78119
    </address>

    <div class="divider"></div>

    <ul class="contacts">
      <li class="contacts__item">512 555 0148
        <svg viewBox="0 0 24 24"><path d="M3 9c0-3 4-5 9-5s9 2 9 5v2h-5V9H8v2H3z M6 12h12l2 8H4z"/></svg></li>
      <li class="contacts__item">818 555 0192
        <svg viewBox="0 0 24 24"><path d="M7 2h10a1 1 0 0 1 1 1v18a1 1 0 0 1-1 1H7a1 1 0 0 1-1-1V3a1 1 0 0 1 1-1zm1 3v13h8V5z"/></svg></li>
      <li class="contacts__item">t.wrenfeld@ValmiraHealth.example
        <svg viewBox="0 0 24 24"><path d="M2 6h20v12H2z"/><path class="icon-cut" d="M2 6l10 7 10-7" stroke-width="1.6"/></svg></li>
      <li class="contacts__item">www.ValmiraHealth.example
        <svg viewBox="0 0 24 24"><circle cx="12" cy="12" r="9"/><path class="icon-cut" d="M3 12h18M12 3c3 3 3 15 0 18M12 3c-3 3-3 15 0 18" stroke-width="1.4"/></svg></li>
    </ul>
  </section>
</body>
</html>
```